New Innovative Counselling and psychotherapy Service needs Business Card design

Keep it simple and professional. On one side, just company name and logo (perhaps in all blue) and maybe a tag line.

On other side (all white) my name and Qualifications in centre

Industry/Entity Type

Health And Wellness

Contact Information for Business Card

Dara Whelby
Counsellor & Psychotherapist
BSc (Psychol.), BA, Dip. (Couns. & Psych.), PG.Cert (CBT), FGTrK, ONRE

I will also require Mobile no, Email and web site address of which I'll pass on to final designer.

Font styles to use
Sans Serif

Requirements
Must have
• My Logo Only and please use the colours in logo that is in it.
Should not have
• Any other images

```html
<!DOCTYPE html>
<html lang="en">
<head>
<meta charset="utf-8">
<title>Harbor Lane – Business Card</title>
<link rel="stylesheet" href="https://fonts.googleapis.com/css2?family=Arimo:wght@400;700&display=swap">
<style>
  :root {
    --backdrop: #c6c6c6;
    --card-white: #f3f3f3;
    --card-dark: #333333;
    --brand-blue: #45b3ed;
    --brand-green: #8fd15a;
    --ink: #3a3a3a;
    --ink-soft: #4a4a4a;
    --rule: #c9c9c9;
    --white: #ffffff;
  }
  * { margin: 0; padding: 0; box-sizing: border-box; }
  html, body {
    width: 1200px; height: 960px; overflow: hidden;
    background: var(--backdrop);
    font-family: "Arimo", Arial, sans-serif;
  }
  .canvas { position: relative; width: 1200px; height: 960px; }

  .card { position: absolute; width: 600px; overflow: hidden; }

  /* Front */
  .card--front { left: 322px; top: 110px; height: 343px; background: var(--card-white); }
  .brand { position: absolute; left: 31px; top: 144px; display: flex; align-items: center; gap: 14px; }
  .brand__dot { width: 48px; height: 48px; border-radius: 50%; background: var(--brand-blue); }
  .brand__name { font-size: 25px; font-weight: 400; color: var(--ink-soft); letter-spacing: 0.2px; }
  .divider { position: absolute; left: 298px; top: 102px; width: 1px; height: 144px; background: var(--rule); }
  .details { position: absolute; left: 320px; top: 96px; color: var(--ink); }
  .details__name { font-size: 24px; color: var(--brand-blue); line-height: 28px; }
  .details__name strong { font-weight: 700; }
  .details__role { font-size: 15px; line-height: 18px; margin-top: 3px; }
  .details__quals { font-size: 12px; line-height: 15px; margin-top: 2px; }
  .contact { list-style: none; margin-top: 14px; }
  .contact li { display: flex; align-items: center; gap: 8px; font-size: 14.5px; line-height: 19.5px; color: var(--ink-soft); }
  .contact svg { width: 13px; height: 13px; flex: none; fill: var(--brand-blue); }
  .edge-green { position: absolute; left: 0; right: 0; top: 327px; height: 2px; background: var(--brand-green); }
  .edge-blue { position: absolute; left: 0; right: 0; top: 331px; height: 12px; background: var(--brand-blue); }

  /* Back */
  .card--back { left: 320px; top: 493px; height: 342px; background: var(--card-dark); }
  .emblem { position: absolute; left: 0; right: 0; top: 84px; display: flex; flex-direction: column; align-items: center; gap: 18px; }
  .emblem__dot { width: 110px; height: 110px; border-radius: 50%; background: var(--brand-blue); }
  .emblem__name { font-size: 30px; font-weight: 400; color: var(--white); }
  .tagline { position: absolute; left: 0; right: 0; top: 288px; text-align: center; font-size: 14.5px; color: var(--white); }
</style>
</head>
<body>
<main class="canvas">
  <section class="card card--front">
    <div class="brand">
      <span class="brand__dot"></span>
      <span class="brand__name">Harbor Lane</span>
    </div>
    <div class="divider"></div>
    <div class="details">
      <h1 class="details__name"><strong>Dara</strong> Whelby</h1>
      <p class="details__role">Counsellor &amp; Psychotherapist</p>
      <p class="details__quals">BSc (Psychol.), BA, Dip. (Couns. &amp; Psych.)<br>PG.Cert (CBT), FGTrK,</p>
      <ul class="contact">
        <li><svg viewBox="0 0 13 13"><rect x="3" y="0" width="7" height="13" rx="1.5"/><rect x="4.3" y="1.6" width="4.4" height="8.4" fill="#f3f3f3"/></svg>555 201 7730</li>
        <li><svg viewBox="0 0 13 13"><rect x="0" y="2.5" width="13" height="8.5" rx="1"/><path d="M0.8 3.3 L6.5 7.5 L12.2 3.3" stroke="#f3f3f3" stroke-width="1.2" fill="none"/></svg>dara@Harborlane.com</li>
        <li><svg viewBox="0 0 13 13"><circle cx="6.5" cy="6.5" r="6.2"/><path d="M3 4 Q5 3 6 5 T9 8 M7 10 Q8 11 10 10" stroke="#f3f3f3" stroke-width="1.1" fill="none"/></svg>www.Harborlane.com</li>
      </ul>
    </div>
    <div class="edge-green"></div>
    <div class="edge-blue"></div>
  </section>

  <section class="card card--back">
    <div class="emblem">
      <span class="emblem__dot"></span>
      <span class="emblem__name">Harbor Lane</span>
    </div>
    <p class="tagline">Caring For Your Psychological Well-Being Is Our Top Priority</p>
  </section>
</main>
</body>
</html>
```